Corvane Holdings , new business card design

investment firm with corporate clients . need double sided business card , vertical and horizontal options ,logo must be clear. prefer pantone colors only and sharp design. website also www.corvane.ae

Khalid Bin Tarrafi
Managing Director
Tel. +971 4 387 2940
Mobile +971 50 518 2403
khalid@corvane.ae
Q-Span Plaza, officw 18-B07, Warqa Gardens, Dubai

Contact Information for Business Card

Khalid Bin Tarrafi
Managing Director

Font styles to use
Serif

Colors

Designer to choose colors to be used in the design.

```html
<!DOCTYPE html>
<html lang="en">
<head>
<meta charset="utf-8">
<title>Corvane Holdings — Business Card</title>
<link rel="stylesheet" href="https://fonts.googleapis.com/css2?family=Roboto:wght@300;400;700&display=swap">
<style>
  :root {
    --backdrop: #e6e4e0;
    --card-blue: #4e79a5;
    --card-blue-light: #6a93bb;
    --card-white: #f6f6f5;
    --ink-white: #ffffff;
    --ink-dark: #1d2430;
    --ink-grey: #555b63;
    --accent-blue: #4e79a5;
  }
  * { margin: 0; padding: 0; box-sizing: border-box; }
  html, body {
    width: 1200px; height: 911px; overflow: hidden;
    background: var(--backdrop);
    font-family: "Roboto", Arial, sans-serif;
  }
  .canvas {
    position: relative; width: 1200px; height: 911px;
    display: flex; align-items: center; justify-content: center; gap: 70px;
  }
  .card { box-shadow: 0 10px 30px rgba(0,0,0,.18); position: relative; }

  /* Vertical blue side */
  .card--front {
    width: 360px; height: 600px;
    background: linear-gradient(160deg, var(--card-blue) 0%, var(--card-blue-light) 55%, var(--card-blue) 100%);
    color: var(--ink-white);
    padding: 70px 36px 0 36px;
  }
  .brand { display: flex; align-items: center; gap: 10px; }
  .brand__mark { width: 12px; height: 12px; background: currentColor; flex: none; }
  .brand__name {
    font-weight: 300; text-transform: uppercase; letter-spacing: .22em;
  }
  .card--front .brand { justify-content: flex-end; color: var(--ink-white); }
  .card--front .brand__name { font-size: 22px; }

  .person { margin-top: 130px; }
  .person__name { font-weight: 700; font-size: 19px; text-transform: uppercase; letter-spacing: .01em; }
  .person__role { font-weight: 700; font-size: 14px; text-transform: uppercase; color: var(--ink-dark); margin-top: 2px; }

  .contact { list-style: none; margin-top: 22px; }
  .contact__item { display: flex; align-items: center; gap: 12px; font-size: 15px; line-height: 1; margin-bottom: 7px; }
  .contact__icon {
    width: 20px; height: 20px; background: var(--ink-white); border-radius: 3px;
    display: flex; align-items: center; justify-content: center; flex: none;
  }
  .contact__icon svg { width: 14px; height: 14px; }

  .address { margin-top: 26px; font-size: 15px; line-height: 1.3; font-style: normal; }

  /* Horizontal white side */
  .card--back {
    width: 600px; height: 360px;
    background: var(--card-white);
    display: flex; flex-direction: column; align-items: center; justify-content: center;
  }
  .card--back .brand { color: var(--ink-dark); }
  .card--back .brand__mark { background: var(--accent-blue); }
  .card--back .brand__name { font-size: 34px; }
  .card--back .tagline-bar {
    margin-top: 12px; width: 330px; height: 18px; background: var(--accent-blue);
  }
  .web {
    margin-top: 60px; font-size: 14px; letter-spacing: .8em; color: var(--ink-grey);
    font-weight: 400;
  }
</style>
</head>
<body>
<main class="canvas">

  <section class="card card--front" aria-label="Card front, vertical">
    <div class="brand">
      <span class="brand__mark"></span>
      <span class="brand__name">Corvane Holdings</span>
    </div>

    <div class="person">
      <h1 class="person__name">Khalid Bin Tarrafi</h1>
      <p class="person__role">Managing Director</p>
    </div>

    <ul class="contact">
      <li class="contact__item">
        <span class="contact__icon"><svg viewBox="0 0 24 24"><path fill="#1d2430" d="M6.6 10.8a15 15 0 0 0 6.6 6.6l2.2-2.2c.3-.3.7-.4 1-.2 1.1.4 2.3.6 3.6.6.6 0 1 .4 1 1V20c0 .6-.4 1-1 1A17 17 0 0 1 3 4c0-.6.4-1 1-1h3.5c.6 0 1 .4 1 1 0 1.3.2 2.5.6 3.6.1.3 0 .7-.2 1z"/></svg></span>
        +971 4 387 2940
      </li>
      <li class="contact__item">
        <span class="contact__icon"><svg viewBox="0 0 24 24"><rect x="6" y="2" width="12" height="20" rx="2" fill="none" stroke="#1d2430" stroke-width="2.4"/><circle cx="12" cy="18" r="1.3" fill="#1d2430"/></svg></span>
        +971 50 518 2403
      </li>
      <li class="contact__item">
        <span class="contact__icon"><svg viewBox="0 0 24 24"><rect x="2" y="5" width="20" height="14" fill="#1d2430"/><path d="M2 5l10 8 10-8" fill="none" stroke="#fff" stroke-width="1.8"/></svg></span>
        khalid@corvane.ae
      </li>
      <li class="contact__item">
        <span class="contact__icon"><svg viewBox="0 0 24 24"><circle cx="12" cy="12" r="10" fill="#1d2430"/><path d="M2 12h20M12 2c3 3 3 17 0 20M12 2c-3 3-3 17 0 20" fill="none" stroke="#fff" stroke-width="1.4"/></svg></span>
        www.corvane.ae
      </li>
    </ul>

    <address class="address">
      Q-Span Plaza, officw 18-B07<br>
      Warqa Gardens, Dubai
    </address>
  </section>

  <section class="card card--back" aria-label="Card back, horizontal">
    <div class="brand">
      <span class="brand__mark"></span>
      <span class="brand__name">Corvane Holdings</span>
    </div>
    <div class="tagline-bar"></div>
    <p class="web">www.corvane.ae</p>
  </section>

</main>
</body>
</html>
```